Redesign Two Website Pages (Homepage & Features) — Modern, Responsive, and Visually Engaging

We’re looking to redesign two pages of our website:

Homepage: https://velmorta.com
Features Page: https://velmorta.com/features

We already have a preliminary design in Figma for the homepage, but it currently feels too plain. Please don’t use this Figma file provided. It was only shared for facilitate using the current website content and not as a source for inspiration. Use your creativity to bring something fresh and less dull as the current design.

We want to enhance it with visually engaging elements, such as illustrations, graphics, or images that align with the content and the application’s purpose, making the design more dynamic and marketing-oriented.

Requirements:
- Create modern, visually appealing designs for both pages.
- Include relevant visuals (images or vector graphics) that complement the content and improve user engagement.
- Ensure full responsiveness across all major viewports: desktop, tablet, and mobile.
- Deliver the final design in Figma format.
- You can choose any colour palette that best fits the concept, but please retain the existing content from the live website.
- We’re looking for a clean, modern, and commercially appealing design that effectively communicates the value of our product.

Target Market(s)

B2B

Number of Pages Required

2 page

Font styles to use
Sans Serif

Requirements
Must have
• Images and graphics to make the design and product more attractive.

```html
<!DOCTYPE html>
<html lang="en">
<head>
<meta charset="utf-8">
<title>VELMORTA — Audit platform</title>
<link href="https://fonts.googleapis.com/css2?family=Poppins:wght@300;400;500;600;700&display=swap" rel="stylesheet">
<style>
:root{
  --blue:#0a6fd6;
  --blue-dark:#0757b0;
  --ink:#1b1e24;
  --muted:#5d6470;
  --line:#c9d3df;
  --pale:#e8f1fb;
  --pale-2:#f2f6fb;
  --white:#ffffff;
  --red:#e0312f;
  --green:#2a9a58;
}
*{box-sizing:border-box;margin:0;padding:0}
html,body{width:1200px;height:4228px;overflow:hidden}
body{font-family:"Poppins",sans-serif;color:var(--ink);background:var(--white);position:relative}
.abs{position:absolute}
a{color:inherit;text-decoration:none}
.btn{display:inline-flex;align-items:center;justify-content:center;height:36px;padding:0 16px;border-radius:4px;font-size:14px;font-weight:500}
.btn-solid{background:var(--blue);color:var(--white)}
.btn-ghost{border:1.5px solid var(--blue);color:var(--blue);background:var(--white)}
.h-light{font-weight:300;font-size:40px;line-height:1.2;color:var(--ink)}
.h-bold{font-weight:700;font-size:40px;line-height:1.2;color:var(--blue)}
.brand{display:flex;align-items:center;gap:10px}
.brand-mark{width:26px;height:26px;background:var(--blue);border-radius:4px}
.brand-name{font-weight:500;font-size:18px;line-height:1;color:var(--ink)}
.brand-tag{font-size:12px;color:var(--ink);margin-top:3px}

/* header & hero */
.hero-bg{left:0;top:0;width:1200px;height:616px;background:var(--pale);overflow:hidden}
.hero-circle{left:672px;top:-270px;width:760px;height:760px;border-radius:50%;background:#d9e8f8}
.header{left:0;top:0;width:1200px;height:85px;border-bottom:1px solid #c5d9ee}
.nav{right:112px;top:24px;display:flex;align-items:center;gap:30px;font-size:15px}
.nav .sep{width:1px;height:36px;background:var(--ink);opacity:.5}
.nav .btns{display:flex;gap:16px}
.trusted{left:112px;top:152px;font-size:19px;color:var(--ink);display:flex;align-items:center;gap:8px}
.trusted b{color:var(--blue);font-weight:400}
.hero-title{left:112px;top:182px}
.hero-title .h-light,.hero-title .h-bold{font-size:46px}
.hero-copy{left:112px;top:318px;width:500px;font-size:15px;line-height:1.72}
.hero-btns{left:112px;top:442px;display:flex;gap:16px}
.hero-note{left:112px;top:487px;font-size:12px;color:var(--muted)}
.hero-photo{left:686px;top:120px;width:410px;height:456px;border-radius:200px 200px 0 0;background:linear-gradient(180deg,#c7d9ee 0%,#2f55b9 70%,#1f3f94 100%)}

.stats{left:159px;top:575px;width:882px;height:151px;background:var(--white);border-radius:14px;box-shadow:0 10px 30px rgba(30,70,130,.12);display:flex;align-items:center}
.stat{flex:1;text-align:center;border-right:1.5px solid #3a3f47}
.stat:last-child{border-right:0}
.stat strong{display:block;font-size:34px;font-weight:600}
.stat span{font-size:16px;color:var(--muted)}

/* compare */
.sec-head{left:0;width:1200px;text-align:center}
.sec-sub{font-size:15px}
.compare{left:158px;top:977px;width:885px;height:284px;border:1.5px solid var(--blue);border-radius:14px;overflow:hidden;display:flex}
.col{flex:1}
.col-head{height:70px;background:var(--blue);color:var(--white);font-size:21px;font-weight:600;display:flex;align-items:center;padding-left:26px}
.col:first-child .col-head{border-right:5px solid var(--white)}
.col-body{padding:36px 28px;font-size:15px;height:214px}
.col.after .col-body{background:var(--pale)}
.col-body li{list-style:none;display:flex;align-items:center;gap:14px;margin-bottom:17px}
.x{color:var(--red);font-weight:600;width:14px}
.tick{width:16px;height:16px}

/* features */
.sec-left{left:112px}
.features{left:112px;top:1519px;width:977px;height:509px;display:grid;grid-template-columns:330px 340px 307px;grid-template-rows:246px 263px}
.feat{padding:4px 20px 0 0}
.feat.mid{padding-left:32px;border-left:1.5px solid var(--line);border-right:1.5px solid var(--line)}
.feat.end{padding-left:32px}
.feat.top{border-bottom:1.5px solid var(--line)}
.feat.bot{padding-top:42px}
.feat svg{width:52px;height:52px;margin-bottom:8px}
.feat h3{font-size:19px;font-weight:500;margin-bottom:8px}
.feat p{font-size:13.5px;line-height:1.65;color:var(--muted);height:72px}
.feat a{display:inline-block;margin-top:12px;font-size:14px;color:var(--blue);border-bottom:1px solid var(--blue)}

/* testimonials */
.testi-bg{left:0;top:2105px;width:1200px;height:613px;background:linear-gradient(160deg,#eef3f9,#e3ebf5)}
.quote{top:2353px;width:304px;height:233px;background:#f4f7fb;border:1.5px solid #8c96a3;border-radius:12px;padding:28px 24px}
.stars{color:#f5b400;font-size:15px;letter-spacing:1px}
.qmark{right:20px;top:10px;font-size:54px;font-weight:700;color:var(--blue);line-height:1}
.quote p{font-size:12px;line-height:1.8;color:var(--muted);margin-top:8px;height:100px}
.quote .who{font-size:14px;font-weight:500;margin-top:14px}
.quote .role{font-size:10px;color:var(--muted)}
.dots{left:564px;top:2617px;display:flex;gap:8px;align-items:center}
.dots i{width:9px;height:9px;border-radius:50%;background:#4a5260}
.dots i:first-child{width:14px;height:14px;background:var(--blue)}

/* pricing */
.toggle{left:878px;top:2911px;display:flex;align-items:center;gap:16px;font-size:17px;font-weight:500}
.switch{width:52px;height:22px;border-radius:11px;background:var(--blue);position:relative}
.switch::after{content:"";position:absolute;right:3px;top:3px;width:16px;height:16px;border-radius:50%;background:var(--white)}
.plan{top:2993px;width:309px;height:562px;border:1.5px solid #b9d0ea;border-radius:12px;padding:26px 22px;background:var(--white)}
.plan.pro{background:var(--pale);border-color:var(--pale)}
.plan h4{font-size:24px;font-weight:600;color:var(--blue)}
.plan .desc{font-size:13px;color:var(--muted);line-height:1.35;margin-top:8px;height:54px}
.price{font-size:30px;font-weight:500}
.price small{font-size:14px;color:var(--muted);font-weight:400}
.per{font-size:13px;color:var(--muted)}
.plan .btn{width:264px;margin-top:16px;height:34px}
.plan hr{border:0;border-top:1px solid var(--line);margin:26px 0 20px}
.plan h5{font-size:17px;font-weight:500;margin-bottom:12px}
.plan li{list-style:none;display:flex;align-items:center;gap:14px;font-size:13px;margin-bottom:11px}
.scroll{position:absolute;right:18px;top:330px;width:6px;height:176px;border:1px solid #7a8592;border-radius:3px}
.scroll::after{content:"";position:absolute;left:1px;top:2px;width:2px;height:56px;background:var(--blue)}
.arrow{top:3252px;width:24px;height:40px}

/* cta */
.cta-bg{left:0;top:3793px;width:1200px;height:435px;background:var(--pale-2)}
.cta{left:112px;top:3691px;width:977px;height:204px;background:var(--white);border-radius:14px;box-shadow:0 8px 30px rgba(30,70,130,.10);padding:40px 42px}
.cta-btns{right:40px;top:84px;display:flex;gap:16px}

/* footer */
.foot-col h6{font-size:20px;font-weight:500;margin-bottom:14px}
.foot-col li{list-style:none;font-size:15px;margin-bottom:8px}
.foot-line{left:112px;top:4164px;width:977px;border-top:1.5px solid #8a94a0}
.copy{left:0;width:1200px;top:4186px;text-align:center;font-size:12px}
.to-top{left:1107px;top:4182px;width:38px;height:38px;border-radius:50%;background:var(--blue);display:flex;align-items:center;justify-content:center}
</style>
</head>
<body>

<div class="abs hero-bg"><div class="abs hero-circle"></div></div>

<header class="abs header">
  <div class="abs brand" style="left:112px;top:24px">
    <span class="brand-mark"></span>
    <div><div class="brand-name">VELMORTA</div><div class="brand-tag">Guiding every audit with clarity</div></div>
  </div>
  <nav class="abs nav">
    <a href="#">Features</a><a href="#">Pricing</a><a href="#">Demo</a>
    <span class="sep"></span>
    <span class="btns"><a class="btn btn-ghost" href="#">Sign Up</a><a class="btn btn-solid" href="#">Sign In</a></span>
  </nav>
</header>

<div class="abs trusted">
  <svg class="tick" viewBox="0 0 16 16"><path d="M2 8l4 4 8-8" fill="none" stroke="#0a6fd6" stroke-width="2"/></svg>
  Trusted by <b>300+ audit firms worldwide</b>
</div>
<div class="abs hero-title">
  <div class="h-light">Cut Audit Time by 60%</div>
  <div class="h-bold">Without Cutting Corners</div>
</div>
<p class="abs hero-copy">The only audit platform that combines AI-powered template generation, real-time collaboration, and intelligent compliance tracking. Join leading firms completing audits 3x faster with 99.9% accuracy.</p>
<div class="abs hero-btns"><a class="btn btn-solid" href="#">Start Free Trial</a><a class="btn btn-ghost" href="#">Schedule Demo</a></div>
<div class="abs hero-note">No credit card required • 14-day free trial • Cancel anytime</div>
<div class="abs hero-photo" role="img" aria-label="Smiling auditor in a blue work shirt holding an open laptop"></div>

<div class="abs stats">
  <div class="stat"><strong>300+</strong><span>Audit Firms</span></div>
  <div class="stat"><strong>1000+</strong><span>Audits Completed</span></div>
  <div class="stat"><strong>99.9%</strong><span>Compliance Rate</span></div>
  <div class="stat"><strong>4.9/5</strong><span>Customer Rating</span></div>
</div>

<div class="abs sec-head" style="top:802px">
  <div class="h-light" style="font-size:38px">Stop Losing $50K+ Per Year</div>
  <div class="h-bold" style="font-size:38px">On Manual Audits</div>
  <p class="sec-sub" style="margin-top:10px">Your team spends 70% of audit time on repetitive tasks. We fix that.</p>
</div>

<div class="abs compare">
  <div class="col">
    <div class="col-head">Without VELMORTA</div>
    <ul class="col-body">
      <li><span class="x">✕</span>200+ hours creating templates from scratch</li>
      <li><span class="x">✕</span>Version control chaos with Excel spreadsheets</li>
      <li><span class="x">✕</span>60% error rate from manual data entry</li>
      <li><span class="x">✕</span>Compliance violations risk $100K+ fines</li>
    </ul>
  </div>
  <div class="col after">
    <div class="col-head">With VELMORTA</div>
    <ul class="col-body">
      <li><svg class="tick" viewBox="0 0 16 16"><path d="M2 8l4 4 8-8" fill="none" stroke="#2a9a58" stroke-width="2"/></svg>AI generates templates in 30 seconds</li>
      <li><svg class="tick" viewBox="0 0 16 16"><path d="M2 8l4 4 8-8" fill="none" stroke="#2a9a58" stroke-width="2"/></svg>Real-time collaboration with audit trail</li>
      <li><svg class="tick" viewBox="0 0 16 16"><path d="M2 8l4 4 8-8" fill="none" stroke="#2a9a58" stroke-width="2"/></svg>Automated validation catches 99% of errors</li>
      <li><svg class="tick" viewBox="0 0 16 16"><path d="M2 8l4 4 8-8" fill="none" stroke="#2a9a58" stroke-width="2"/></svg>Built-in compliance for ISO, GDPR, PCI DSS</li>
    </ul>
  </div>
</div>

<div class="abs sec-left" style="top:1336px">
  <div class="h-light" style="font-size:38px">Everything You Need to Scale</div>
  <div class="h-bold" style="font-size:38px">Your Audit Practice</div>
  <p class="sec-sub" style="margin-top:8px">From solo practitioners to Big 4 firms, we've built the features that matter</p>
</div>

<div class="abs features">
  <div class="feat top">
    <svg viewBox="0 0 52 52"><path d="M20 8l4 12 12 4-12 4-4 12-4-12-12-4 12-4z" fill="#0a6fd6"/><path d="M40 2l2 6 6 2-6 2-2 6-2-6-6-2 6-2z" fill="#0a6fd6"/><path d="M38 36l2 5 5 2-5 2-2 5-2-5-5-2 5-2z" fill="#0a6fd6"/></svg>
    <h3>AI-Powered Templates</h3>
    <p>Generate industry-specific audit templates in 30 seconds. Our AI knows ISO 27001, GDPR, PCI DSS, and 50+ frameworks.</p>
    <a href="#">Save 200+ hours per year</a>
  </div>
  <div class="feat top mid">
    <svg viewBox="0 0 52 52"><circle cx="24" cy="24" r="18" fill="none" stroke="#0a6fd6" stroke-width="6" stroke-dasharray="6 4"/><circle cx="24" cy="24" r="11" fill="none" stroke="#0a6fd6" stroke-width="3"/><path d="M24 18v7h5" stroke="#0a6fd6" stroke-width="3" fill="none"/><circle cx="40" cy="40" r="9" fill="#0a6fd6"/><path d="M36 40l3 3 5-5" stroke="#fff" stroke-width="2" fill="none"/></svg>
    <h3>Real-Time Collaboration</h3>
    <p>Your entire team works together seamlessly. See changes instantly, leave comments, and track who did what.</p>
    <a href="#">3x faster team audits</a>
  </div>
  <div class="feat top end">
    <svg viewBox="0 0 52 52"><path d="M6 4h24l8 8v34H6z" fill="none" stroke="#0a6fd6" stroke-width="3"/><path d="M11 14h14M11 20h18M11 38h10" stroke="#0a6fd6" stroke-width="3"/><circle cx="34" cy="32" r="9" fill="#fff" stroke="#0a6fd6" stroke-width="3"/><path d="M40 38l8 8" stroke="#0a6fd6" stroke-width="4"/></svg>
    <h3>Evidence Management</h3>
    <p>Attach documents, screenshots, and recordings directly to audit items. Never lose critical evidence again.</p>
    <a href="#">100% audit trail coverage</a>
  </div>
  <div class="feat bot">
    <svg viewBox="0 0 52 52"><rect x="2" y="16" width="16" height="16" rx="2" fill="#0a6fd6"/><rect x="32" y="2" width="16" height="16" rx="2" fill="#0a6fd6"/><rect x="32" y="32" width="16" height="16" rx="2" fill="#0a6fd6"/><path d="M18 24h7V10h7M25 24v16h7" stroke="#0a6fd6" stroke-width="3" fill="none"/></svg>
    <h3>Automated Workflows</h3>
    <p>Set up once, run forever. Automated reminders, status updates, and report generation keep projects on track.</p>
    <a href="#">Zero missed deadlines</a>
  </div>
  <div class="feat bot mid">
    <svg viewBox="0 0 52 52"><rect x="4" y="32" width="7" height="16" fill="#0a6fd6"/><rect x="15" y="24" width="7" height="24" fill="#0a6fd6"/><rect x="26" y="28" width="7" height="20" fill="#0a6fd6"/><rect x="37" y="16" width="7" height="32" fill="#0a6fd6"/><path d="M4 22l12-10 10 6 16-14" stroke="#0a6fd6" stroke-width="3" fill="none"/></svg>
    <h3>Smart Analytics</h3>
    <p>Spot risks before they become issues. Our dashboard shows completion rates, bottlenecks, and compliance gaps.</p>
    <a href="#">60% fewer compliance issues</a>
  </div>
  <div class="feat bot end">
    <svg viewBox="0 0 52 52"><path d="M22 3l18 7v14c0 12-8 20-18 24C12 44 4 36 4 24V10z" fill="#0a6fd6"/><circle cx="36" cy="36" r="12" fill="#fff" stroke="#0a6fd6" stroke-width="3"/><path d="M30 36l4 4 8-8" stroke="#0a6fd6" stroke-width="3" fill="none"/></svg>
    <h3>Bank-grade Security</h3>
    <p>End to end encryption, role-based access, and complete audit logs protect your data</p>
    <a href="#">Zero security breaches</a>
  </div>
</div>

<div class="abs testi-bg"></div>
<div class="abs sec-head" style="top:2178px">
  <div class="h-light" style="font-size:38px">Audit leaders choose</div>
  <div class="h-bold" style="font-size:38px">VELMORTA</div>
  <p class="sec-sub" style="margin-top:6px">See why we're rated 4.9/5 by 500+ audit professionals.</p>
</div>
<div class="abs quote" style="left:112px">
  <span class="abs qmark">”</span>
  <div class="stars">★★★★★</div>
  <p>“We've reduced audit completion time from 3 weeks to 1 week. The AI templates alone saved us $200K in the first year. This is a game changer for mid size firms.”</p>
  <div class="who">Laura Brennick</div><div class="role">Partner, Brennick &amp; Hale CPA</div>
</div>
<div class="abs quote" style="left:448px">
  <span class="abs qmark">”</span>
  <div class="stars">★★★★★</div>
  <p>“Our compliance rate went from 85% to 99.9%. The platform catches issues we'd never spot manually. We've avoided multiple six-figure penalties.”</p>
  <div class="who">Daniel Ostrova</div><div class="role">Compliance Director, Ledgerline Inc.</div>
</div>
<div class="abs quote" style="left:785px">
  <span class="abs qmark">”</span>
  <div class="stars">★★★★★</div>
  <p>“Best investment we've made. Our team can handle 3x more clients without adding headcount. ROI was positive in month one.”</p>
  <div class="who">Helen Marsh</div><div class="role">Managing Director, Marsh Assurance Group</div>
</div>
<div class="abs dots"><i></i><i></i><i></i><i></i></div>

<div class="abs sec-left" style="top:2792px">
  <div class="h-light" style="font-size:38px">Simple Pricing That Scales</div>
  <div class="h-bold" style="font-size:38px">With You</div>
  <p class="sec-sub" style="margin-top:8px;width:480px;line-height:1.65">Choose the perfect plan for your audit team. All plans include a 14-day free trial.</p>
</div>
<div class="abs toggle">Monthly <span class="switch"></span> Yearly</div>

<svg class="abs arrow" style="left:56px" viewBox="0 0 24 40"><path d="M20 4L4 20l16 16" fill="none" stroke="#1b1e24" stroke-width="3"/></svg>
<svg class="abs arrow" style="left:1122px" viewBox="0 0 24 40"><path d="M4 4l16 16L4 36" fill="none" stroke="#1b1e24" stroke-width="3"/></svg>

<div class="abs plan" style="left:112px">
  <h4>Free Plan</h4>
  <p class="desc">Perfect for getting started with basic auditing needs.</p>
  <div class="price">$0 <small>/month</small></div><div class="per">Up to 2 team members</div>
  <a class="btn btn-solid" href="#">Start Free Trial</a>
  <hr><h5>Includes:</h5>
  <ul>
    <li><svg class="tick" viewBox="0 0 16 16"><path d="M2 8l4 4 8-8" fill="none" stroke="#2a9a58" stroke-width="2"/></svg>2 team members</li>
    <li><svg class="tick" viewBox="0 0 16 16"><path d="M2 8l4 4 8-8" fill="none" stroke="#2a9a58" stroke-width="2"/></svg>5 templates</li>
    <li><svg class="tick" viewBox="0 0 16 16"><path d="M2 8l4 4 8-8" fill="none" stroke="#2a9a58" stroke-width="2"/></svg>10 active projects</li>
    <li><svg class="tick" viewBox="0 0 16 16"><path d="M2 8l4 4 8-8" fill="none" stroke="#2a9a58" stroke-width="2"/></svg>Evidence management</li>
    <li><svg class="tick" viewBox="0 0 16 16"><path d="M2 8l4 4 8-8" fill="none" stroke="#2a9a58" stroke-width="2"/></svg>Basic support</li>
    <li><span class="x">✕</span>Custom templates</li>
    <li><span class="x">✕</span>Advanced analytics</li>
  </ul>
  <span class="scroll"></span>
</div>
<div class="abs plan" style="left:445px">
  <h4>Started</h4>
  <p class="desc">Perfect for small audit teams and solo practitioners.</p>
  <div class="price">$15 <small>/month</small></div><div class="per">$15/user x 1 user</div>
  <a class="btn btn-solid" href="#">Start Free Trial</a>
  <hr><h5>Includes:</h5>
  <ul>
    <li><svg class="tick" viewBox="0 0 16 16"><path d="M2 8l4 4 8-8" fill="none" stroke="#2a9a58" stroke-width="2"/></svg>Unlimited team members</li>
    <li><svg class="tick" viewBox="0 0 16 16"><path d="M2 8l4 4 8-8" fill="none" stroke="#2a9a58" stroke-width="2"/></svg>10 active audits</li>
    <li><svg class="tick" viewBox="0 0 16 16"><path d="M2 8l4 4 8-8" fill="none" stroke="#2a9a58" stroke-width="2"/></svg>Evidence management</li>
    <li><svg class="tick" viewBox="0 0 16 16"><path d="M2 8l4 4 8-8" fill="none" stroke="#2a9a58" stroke-width="2"/></svg>Basic support</li>
    <li><svg class="tick" viewBox="0 0 16 16"><path d="M2 8l4 4 8-8" fill="none" stroke="#2a9a58" stroke-width="2"/></svg>Email support</li>
    <li><span class="x">✕</span>Custom templates</li>
    <li><span class="x">✕</span>Advanced analytics</li>
  </ul>
  <span class="scroll"></span>
</div>
<div class="abs plan pro" style="left:778px">
  <h4>Professional</h4>
  <p class="desc">Ideal for growing audit firms with multiple clients.</p>
  <div class="price">$39 <small>/month</small></div><div class="per">$39/user x 1 user</div>
  <a class="btn btn-solid" href="#">Start Free Trial</a>
  <hr><h5>Includes:</h5>
  <ul>
    <li><svg class="tick" viewBox="0 0 16 16"><path d="M2 8l4 4 8-8" fill="none" stroke="#2a9a58" stroke-width="2"/></svg>Unlimited team members</li>
    <li><svg class="tick" viewBox="0 0 16 16"><path d="M2 8l4 4 8-8" fill="none" stroke="#2a9a58" stroke-width="2"/></svg>Unlimited audits</li>
    <li><svg class="tick" viewBox="0 0 16 16"><path d="M2 8l4 4 8-8" fill="none" stroke="#2a9a58" stroke-width="2"/></svg>Custom templates + AI builder</li>
    <li><svg class="tick" viewBox="0 0 16 16"><path d="M2 8l4 4 8-8" fill="none" stroke="#2a9a58" stroke-width="2"/></svg>Evidence management</li>
    <li><svg class="tick" viewBox="0 0 16 16"><path d="M2 8l4 4 8-8" fill="none" stroke="#2a9a58" stroke-width="2"/></svg>Templates library</li>
    <li><svg class="tick" viewBox="0 0 16 16"><path d="M2 8l4 4 8-8" fill="none" stroke="#2a9a58" stroke-width="2"/></svg>Advanced evidence</li>
    <li><svg class="tick" viewBox="0 0 16 16"><path d="M2 8l4 4 8-8" fill="none" stroke="#2a9a58" stroke-width="2"/></svg>AI powered scoring</li>
  </ul>
  <span class="scroll"></span>
</div>
<p class="abs" style="left:0;width:1200px;top:3588px;text-align:center;font-size:14px">All plans include: SSL encryption, daily backups, 99.9% uptime SLA</p>

<div class="abs cta-bg"></div>
<div class="abs cta">
  <div class="h-light" style="font-size:38px">Ready to Transform</div>
  <div class="h-bold" style="font-size:38px">Your Audit Practice?</div>
  <p style="font-size:15px;margin-top:8px">Join hundreds of companies saving time and money with VELMORTA</p>
  <div class="abs cta-btns"><a class="btn btn-solid" href="#">Start Free Trial</a><a class="btn btn-ghost" href="#">Schedule Demo</a></div>
</div>

<footer>
  <div class="abs brand" style="left:112px;top:3985px">
    <span class="brand-mark"></span>
    <div><div class="brand-name">VELMORTA</div><div class="brand-tag">Guiding every audit with clarity</div></div>
  </div>
  <div class="abs foot-col" style="left:493px;top:3984px"><h6>Product</h6><ul><li>Features</li><li>Pricing</li><li>Demo</li><li>Sign In</li></ul></div>
  <div class="abs foot-col" style="left:708px;top:3984px"><h6>Company</h6><ul><li>About</li><li>Contact</li><li>System Status</li></ul></div>
  <div class="abs foot-col" style="left:961px;top:3984px"><h6>Legal</h6><ul><li>Privacy Policy</li><li>Terms of Service</li><li>Security</li><li>Compliance</li></ul></div>
  <div class="abs foot-line"></div>
  <p class="abs copy">© 2025 Quillstone.com. VELMORTA™ – All rights reserved.</p>
  <a class="abs to-top" href="#" aria-label="Back to top"><svg width="18" height="18" viewBox="0 0 18 18"><path d="M9 15V3M3 9l6-6 6 6" fill="none" stroke="#fff" stroke-width="2.4"/></svg></a>
</footer>

</body>
</html>
```